e-commerce store for sport clothing online store "baseball merchandise "web application...

I want to design a UX/UI for my web application website for the online store I will provide you with the following:
1. screen shots of the initial design for the pages>
2. the logo files.
3. The brand guideline file.

the provided files (screen shots) is guideline I want to see CREATIVITY with the UX/UI DESIGN.
PS. PLEASE FOLLOW THE BRANDGUIDE LINE CAREFULLY SPECIALLY THE TYPOGRAPHY & THE COLOR CODES.

PLEASE VISIT THIS WEBSITE brightlane.varomi-qz.com to see more for the screens.

```html
<!DOCTYPE html>
<html lang="en">
<head>
<meta charset="utf-8">
<title>Store App – Side Menu</title>
<link rel="stylesheet" href="https://fonts.googleapis.com/css2?family=Titillium+Web:wght@400;600;700&family=Lato:wght@400;700&display=swap">
<style>
  :root {
    --navy: #0e2246;
    --ink: #0f1f3d;
    --white: #ffffff;
    --stage: #e6e8ec;
    --surface: #f4f4f4;
    --card: #ffffff;
    --muted: #555b66;
    --email: #d7dbe5;
    --accent-red: #b0102e;
    --avatar-orange: #f5a24a;
    --scrim: rgba(0, 0, 0, 0.5);
  }
  * { box-sizing: border-box; margin: 0; padding: 0; }
  html, body {
    width: 831px; height: 1200px; overflow: hidden;
    background: var(--stage);
    font-family: "Titillium Web", sans-serif;
  }
  .screen {
    position: absolute; left: 165px; top: 45px;
    width: 500px; height: 1110px; overflow: hidden;
    background: var(--surface);
  }

  /* Underlying store page */
  .store { position: absolute; inset: 0; }
  .store-bar { position: absolute; left: 0; top: 0; width: 100%; height: 112px; background: var(--navy); }
  .cart-button { position: absolute; left: 438px; top: 40px; width: 34px; height: 30px; }
  .cart-badge {
    position: absolute; left: 462px; top: 32px; width: 18px; height: 18px; border-radius: 50%;
    background: var(--accent-red); color: var(--white); font: 600 11px/18px "Titillium Web", sans-serif; text-align: center;
  }
  .hero { position: absolute; left: 0; top: 112px; width: 100%; height: 249px;
    background: linear-gradient(160deg, #9aa09a 0%, #5d645d 55%, #3a403b 100%); }
  .section-row { position: absolute; left: 0; width: 100%; background: var(--white); }
  .chevron { position: absolute; right: 20px; width: 14px; height: 20px; }
  .product-card { position: absolute; left: 362px; width: 200px; height: 195px; background: var(--card);
    border-radius: 8px; box-shadow: 0 2px 8px rgba(0,0,0,0.12); overflow: hidden; }
  .product-photo { position: absolute; left: 12px; top: 16px; width: 80px; height: 130px; border-radius: 6px;
    background: linear-gradient(180deg, #d9d9d9, #b9b9b9); }
  .product-title { position: absolute; left: 107px; top: 10px; width: 150px;
    font: 700 18px/25px "Lato", sans-serif; color: var(--ink); }
  .product-text { position: absolute; left: 107px; top: 66px; width: 150px;
    font: 400 14px/20px "Lato", sans-serif; color: var(--muted); }
  .add-button { position: absolute; left: 108px; top: 160px; width: 62px; height: 62px; border-radius: 50%; background: var(--accent-red); }
  .scrim { position: absolute; inset: 0; background: var(--scrim); }

  /* Drawer */
  .drawer { position: absolute; left: 0; top: 0; width: 374px; height: 100%; background: var(--white); }
  .drawer-header { position: absolute; left: 0; top: 0; width: 100%; height: 253px; background: var(--navy); }
  .back-arrow { position: absolute; left: 22px; top: 16px; width: 26px; height: 26px; }
  .avatar { position: absolute; left: 39px; top: 53px; width: 110px; height: 110px; border-radius: 50%;
    border: 6px solid var(--white); background: var(--avatar-orange); }
  .user-name { position: absolute; left: 181px; top: 74px; color: var(--white); font: 400 24px/32px "Titillium Web", sans-serif; white-space: nowrap; }
  .user-email { position: absolute; left: 181px; top: 108px; color: var(--email); font: 400 15px/20px "Titillium Web", sans-serif; white-space: nowrap; }
  .menu { list-style: none; }
  .menu-item { position: absolute; left: 36px; display: flex; align-items: center; height: 36px; }
  .menu-icon { width: 30px; height: 30px; margin-right: 31px; fill: var(--ink); }
  .menu-label { font: 700 23px/36px "Titillium Web", sans-serif; color: var(--ink); white-space: nowrap; }
  .copyright { position: absolute; left: 0; width: 100%; top: 1066px; text-align: center;
    font: 700 13px/20px "Titillium Web", sans-serif; color: var(--ink); padding-right: 28px; }
</style>
</head>
<body>
<div class="screen">
  <div class="store">
    <div class="store-bar"></div>
    <svg class="cart-button" viewBox="0 0 24 24" fill="#8a93a8"><path d="M7 18a2 2 0 1 0 0 4 2 2 0 0 0 0-4zm10 0a2 2 0 1 0 0 4 2 2 0 0 0 0-4zM1 2v2h2l3.6 7.6-1.4 2.4A2 2 0 0 0 7 17h12v-2H7.4l1.1-2h7.5a2 2 0 0 0 1.7-1l3.6-6.5A1 1 0 0 0 20.4 4H5.2L4.3 2z"/></svg>
    <div class="cart-badge">1</div>
    <div class="hero" role="img" aria-label="Banner photo of palm trees"></div>

    <div class="section-row" style="top:361px;height:87px"></div>
    <svg class="chevron" style="top:402px" viewBox="0 0 14 20"><path d="M3 2l8 8-8 8" fill="none" stroke="#0f1f3d" stroke-width="3"/></svg>

    <div class="product-card" style="top:466px">
      <div class="product-photo" role="img" aria-label="Printed grey t-shirt"></div>
      <div class="product-title">Misty<br>Flyer Tee</div>
      <div class="product-text">If you love the game, your gear should be something special.</div>
      <div class="add-button"></div>
    </div>

    <div class="section-row" style="top:662px;height:105px"></div>
    <svg class="chevron" style="top:721px" viewBox="0 0 14 20"><path d="M3 2l8 8-8 8" fill="none" stroke="#0f1f3d" stroke-width="3"/></svg>

    <div class="product-card" style="top:784px">
      <div class="product-photo" role="img" aria-label="Grey baseball cap"></div>
      <div class="product-title">Bass Cap</div>
      <div class="product-text">Super light structure with a buckle strap and a low profile.</div>
      <div class="add-button"></div>
    </div>

    <div class="section-row" style="top:980px;height:105px"></div>
    <svg class="chevron" style="top:1039px" viewBox="0 0 14 20"><path d="M3 2l8 8-8 8" fill="none" stroke="#0f1f3d" stroke-width="3"/></svg>
    <div class="scrim"></div>
  </div>

  <nav class="drawer">
    <header class="drawer-header">
      <svg class="back-arrow" viewBox="0 0 24 24"><path d="M20 12H5M11 5l-7 7 7 7" fill="none" stroke="#fff" stroke-width="2.4"/></svg>
      <div class="avatar" role="img" aria-label="User avatar"></div>
      <div class="user-name">User Name</div>
      <div class="user-email">player07@mail.example</div>
    </header>

    <ul class="menu">
      <li class="menu-item" style="top:298px">
        <svg class="menu-icon" viewBox="0 0 24 24"><path d="M12 3L2 12h3v8h14v-8h3z"/></svg>
        <span class="menu-label">Home</span>
      </li>
      <li class="menu-item" style="top:394px">
        <svg class="menu-icon" viewBox="0 0 24 24"><path d="M7 18a2 2 0 1 0 0 4 2 2 0 0 0 0-4zm10 0a2 2 0 1 0 0 4 2 2 0 0 0 0-4zM1 2v2h2l3.6 7.6-1.4 2.4A2 2 0 0 0 7 17h12v-2H7.4l1.1-2h7.5a2 2 0 0 0 1.7-1l3.6-6.5A1 1 0 0 0 20.4 4H5.2L4.3 2z"/></svg>
        <span class="menu-label">My Cart</span>
      </li>
      <li class="menu-item" style="top:490px">
        <svg class="menu-icon" viewBox="0 0 24 24"><path d="M1 5h14v11H1zM15 9h4l3 4v3h-7z"/><circle cx="5" cy="18" r="2.2"/><circle cx="18" cy="18" r="2.2"/></svg>
        <span class="menu-label">Track Oders</span>
      </li>
      <li class="menu-item" style="top:584px">
        <svg class="menu-icon" viewBox="0 0 24 24"><path d="M19.4 13a7.5 7.5 0 0 0 0-2l2.1-1.6-2-3.5-2.5 1a7.6 7.6 0 0 0-1.7-1L15 3h-4l-.4 2.7a7.6 7.6 0 0 0-1.7 1l-2.5-1-2 3.5L6.5 11a7.5 7.5 0 0 0 0 2l-2.1 1.6 2 3.5 2.5-1a7.6 7.6 0 0 0 1.7 1L11 21h4l.4-2.7a7.6 7.6 0 0 0 1.7-1l2.5 1 2-3.5zM13 15.5a3.5 3.5 0 1 1 0-7 3.5 3.5 0 0 1 0 7z"/></svg>
        <span class="menu-label">Settings</span>
      </li>
      <li class="menu-item" style="top:685px">
        <svg class="menu-icon" viewBox="0 0 24 24"><circle cx="8" cy="7" r="4"/><path d="M0 21c0-5 3.5-7.5 8-7.5s8 2.5 8 7.5zM17 6h6v2h-6zM17 10h6v2h-6zM18 14h5v2h-5z"/></svg>
        <span class="menu-label">Contact</span>
      </li>
      <li class="menu-item" style="top:779px">
        <svg class="menu-icon" viewBox="0 0 24 24"><path d="M4 2h12v7h-2V4H6v16h8v-5h2v7H4z"/><path d="M10 11h8V8l5 4-5 4v-3h-8z"/></svg>
        <span class="menu-label">Log Out</span>
      </li>
    </ul>

    <div class="copyright">© Basepath 2022</div>
  </nav>
</div>
</body>
</html>
```